Business Card For Halvenmoor Financial Consulting

Hi, I would like a business card designed. Bold, modern.
Please use the same design as the logo. I have also attached the website design to see the overall theme.
Wordmark Font
Color: Hex: #01AEF7

```html
<!DOCTYPE html>
<html lang="en">
<head>
<meta charset="utf-8">
<title>Halvenmoor Consulting – Business Card</title>
<link href="https://fonts.googleapis.com/css2?family=Montserrat:wght@700;800&family=Arimo:ital,wght@0,400;1,400&display=swap" rel="stylesheet">
<style>
  :root {
    --stage: #0b0c0e;
    --card: #121c26;
    --card-edge: #0e161e;
    --accent: #01aef7;
    --ink: #ffffff;
    --muted: #d9e2ea;
  }
  * { box-sizing: border-box; margin: 0; padding: 0; }
  html, body { width: 1200px; height: 963px; overflow: hidden; background: var(--stage); }
  .stage {
    width: 1200px; height: 963px;
    display: flex; flex-direction: column; align-items: center; justify-content: center; gap: 48px;
  }
  .card {
    position: relative;
    width: 720px; height: 411px;
    background: var(--card);
    border-radius: 28px;
    border-bottom: 4px solid var(--accent);
    box-shadow: 0 18px 40px rgba(0,0,0,.6);
    overflow: hidden;
    font-family: "Arimo", Arial, sans-serif;
    color: var(--ink);
  }
  .brand { display: flex; align-items: center; gap: 14px; }
  .brand-square { width: 44px; height: 44px; border: 5px solid var(--accent); flex: none; }
  .brand-name {
    font-family: "Montserrat", Arial, sans-serif; font-weight: 800;
    font-size: 30px; letter-spacing: 2px; line-height: 1; color: var(--ink);
    text-transform: uppercase;
  }
  .brand-name small { display: block; font-size: 12px; letter-spacing: 11px; margin-top: 8px; font-weight: 800; }

  /* front */
  .card-front .brand { position: absolute; right: 44px; top: 64px; }
  .contact { position: absolute; left: 48px; top: 70px; }
  .person-name {
    font-family: "Montserrat", Arial, sans-serif; font-weight: 800;
    font-size: 24px; color: var(--accent); text-transform: uppercase; letter-spacing: .5px;
  }
  .person-role { font-size: 15px; color: var(--ink); margin-top: 2px; }
  .contact-list { list-style: none; margin-top: 26px; }
  .contact-list li { display: flex; align-items: center; gap: 12px; font-size: 15px; margin-bottom: 10px; color: var(--muted); }
  .contact-list svg { width: 16px; height: 16px; fill: var(--accent); flex: none; }
  .divider { position: absolute; left: 48px; right: 48px; top: 250px; height: 1px; background: var(--ink); }
  .address { position: absolute; right: 48px; bottom: 48px; text-align: right; font-size: 16px; line-height: 1.5; }

  /* back */
  .card-back .brand { position: absolute; right: 56px; bottom: 70px; }
</style>
</head>
<body>
<main class="stage">
  <section class="card card-front">
    <div class="contact">
      <p class="person-name">Marcus Ellery</p>
      <p class="person-role">Manager</p>
      <ul class="contact-list">
        <li><svg viewBox="0 0 24 24"><path d="M6.6 10.8a15 15 0 0 0 6.6 6.6l2.2-2.2a1 1 0 0 1 1-.25 11.4 11.4 0 0 0 3.6.57 1 1 0 0 1 1 1V20a1 1 0 0 1-1 1A17 17 0 0 1 3 4a1 1 0 0 1 1-1h3.5a1 1 0 0 1 1 1c0 1.25.2 2.45.57 3.57a1 1 0 0 1-.25 1z"/></svg>123-456-2100</li>
        <li><svg viewBox="0 0 24 24"><path d="M2 5h20v14H2zm2 2v.5l8 5 8-5V7zm0 2.8V17h16V9.8l-8 5z"/></svg>youremail@mailbox.com</li>
        <li><svg viewBox="0 0 24 24"><path d="M12 2a10 10 0 1 0 0 20 10 10 0 0 0 0-20zm6.9 6h-3a15 15 0 0 0-1.3-3.9A8 8 0 0 1 18.9 8zM12 4c.8 1.2 1.5 2.5 1.9 4h-3.8c.4-1.5 1.1-2.8 1.9-4zM4.3 14a8 8 0 0 1 0-4h3.4a16 16 0 0 0 0 4zm.8 2h3a15 15 0 0 0 1.3 3.9A8 8 0 0 1 5.1 16zm3-8h-3a8 8 0 0 1 4.3-3.9C8.8 5.3 8.4 6.6 8.1 8zM12 20c-.8-1.2-1.5-2.5-1.9-4h3.8c-.4 1.5-1.1 2.8-1.9 4zm2.3-6H9.7a14 14 0 0 1 0-4h4.6a14 14 0 0 1 0 4zm.3 5.9c.6-1.2 1-2.5 1.3-3.9h3a8 8 0 0 1-4.3 3.9zM16.3 14a16 16 0 0 0 0-4h3.4a8 8 0 0 1 0 4z"/></svg>www.yourwebsite.com</li>
      </ul>
    </div>
    <div class="brand">
      <span class="brand-square"></span>
      <p class="brand-name">Halvenmoor<small>Consulting</small></p>
    </div>
    <div class="divider"></div>
    <address class="address">Your Address<br>City, State, Zip 0000</address>
  </section>

  <section class="card card-back">
    <div class="brand">
      <span class="brand-square"></span>
      <p class="brand-name">Halvenmoor<small>Consulting</small></p>
    </div>
  </section>
</main>
</body>
</html>
```